Brindle Healthcare Coming Soon Sign

I need a large (10 x5) road banner announcing the construction of our new medical practice at 5187 Larkmoor Road in John's Island. The name of our practice is Brindle Healthcare and we thought it would be fund to nick name it the "Brindle Waystation". We'd like the tagline to read - "There's nothing healthy about driving an hour to see your doctor. So we're coming to you." Opening Late 2025 I have attached three logos as we have two other practices (Brindle Urgent and Brindle Aesthetics ) that should be present on the bottom of the sign but the main business is Brindle Healthcare. For more information on our look/feel visit our website www.goplainway-example.com (which should be somewhere on the banner as well)
Updates

The signage needs to say Coming Late Fall 2025!

Target Market(s)

Drive By traffic must be made aware that we are coming soon

Industry/Entity Type

Healthcare

Requirements
Nice to have
• Western Theme

```html
<!DOCTYPE html>
<html lang="en">
<head>
<meta charset="utf-8">
<title>Brindle Healthcare – Coming Soon Banner</title>
<link rel="stylesheet" href="https://fonts.googleapis.com/css2?family=Montserrat:wght@600;700;800;900&display=swap">
<style>
  :root {
    --navy: #12325a;
    --sky: #62b1e3;
    --white: #ffffff;
    --urgent-red: #e53b34;
    --aesthetic-pink: #e3227d;
    --ink: #2a2f33;
    --page: #ffffff;
  }
  * { box-sizing: border-box; margin: 0; padding: 0; }
  html, body {
    width: 1016px; height: 1200px; overflow: hidden;
    background: var(--page);
    font-family: "Montserrat", Arial, sans-serif;
  }
  .banner {
    position: absolute; left: 28px; top: 360px;
    width: 960px; height: 480px;
    background: var(--white);
    box-shadow: 0 2px 10px rgba(0,0,0,0.18);
    overflow: hidden;
  }
  .accent-bar {
    position: absolute; left: 0; top: 22px;
    width: 8px; height: 185px; background: var(--sky);
  }
  .headline {
    position: absolute; left: 20px; top: 12px;
    font-weight: 900; font-size: 100px; line-height: 94px;
    letter-spacing: -3px; white-space: nowrap;
  }
  .headline .line-navy { color: var(--navy); display: block; }
  .headline .line-sky { color: var(--sky); display: block; }

  .brand-main {
    position: absolute; left: 22px; top: 244px;
    display: flex; align-items: center; gap: 20px;
  }
  .brand-main .mark {
    width: 92px; height: 92px; background: var(--sky);
    border: 5px solid var(--navy); border-radius: 6px;
  }
  .brand-main .name {
    color: var(--navy); font-weight: 700;
    text-transform: uppercase; line-height: 1;
  }
  .brand-main .name .top { display: block; font-size: 46px; letter-spacing: 9px; }
  .brand-main .name .bottom { display: block; font-size: 29px; letter-spacing: 7px; margin-top: 12px; }

  .tagline {
    position: absolute; left: 504px; top: 239px;
    width: 456px; height: 104px;
    background: var(--navy); color: var(--white);
    padding: 9px 14px;
    font-weight: 700; font-size: 22px; line-height: 28px;
    text-transform: uppercase; white-space: nowrap;
  }

  .sub-brand {
    position: absolute; top: 355px;
    display: flex; align-items: center; gap: 14px;
    font-weight: 700; text-transform: uppercase; line-height: 1;
  }
  .sub-brand .mark { width: 38px; height: 38px; border-radius: 50%; }
  .sub-brand .name .top { display: block; font-size: 20px; letter-spacing: 4px; }
  .sub-brand .name .bottom { display: block; font-size: 13px; letter-spacing: 4px; margin-top: 6px; }
  .sub-brand.urgent { left: 540px; }
  .sub-brand.urgent .mark { background: var(--urgent-red); }
  .sub-brand.urgent .name { color: var(--urgent-red); }
  .sub-brand.aesthetics { left: 735px; }
  .sub-brand.aesthetics .mark { background: var(--aesthetic-pink); }
  .sub-brand.aesthetics .name { color: var(--aesthetic-pink); }

  .contact-phone {
    position: absolute; left: 0; top: 412px;
    width: 464px; height: 68px; background: var(--sky);
    display: flex; align-items: center; gap: 10px; padding-left: 22px;
    color: var(--white); font-weight: 800; font-size: 38px; letter-spacing: 0.5px;
  }
  .contact-web {
    position: absolute; left: 471px; top: 412px;
    width: 489px; height: 68px; background: var(--navy);
    display: flex; align-items: center; gap: 12px; padding-left: 28px;
    color: var(--white); font-weight: 800; font-size: 25px;
  }
  .contact-web .domain { color: var(--sky); }
  .icon { flex: none; }
</style>
</head>
<body>
  <main class="banner">
    <div class="accent-bar"></div>

    <h1 class="headline">
      <span class="line-navy">COMING SOON</span>
      <span class="line-sky">LATE FALL 2025!</span>
    </h1>

    <div class="brand-main">
      <div class="mark"></div>
      <div class="name"><span class="top">Brindle</span><span class="bottom">Healthcare</span></div>
    </div>

    <p class="tagline">Conserving rural John's<br>island with home grown<br>progressive primary care</p>

    <div class="sub-brand urgent">
      <div class="mark"></div>
      <div class="name"><span class="top">Brindle</span><span class="bottom">Urgent</span></div>
    </div>

    <div class="sub-brand aesthetics">
      <div class="mark"></div>
      <div class="name"><span class="top">Brindle</span><span class="bottom">Aesthetics</span></div>
    </div>

    <div class="contact-phone">
      <svg class="icon" width="40" height="40" viewBox="0 0 40 40" aria-hidden="true">
        <circle cx="20" cy="20" r="19" fill="var(--white)"/>
        <path d="M13 11 l5 0 l2 6 l-3 2 c1.5 3 3.5 5 6 6 l2 -3 l6 2 l0 5 c-11 1 -19 -7 -18 -18z" fill="var(--sky)"/>
      </svg>
      <span>(555) 014-2290</span>
    </div>

    <div class="contact-web">
      <svg class="icon" width="38" height="38" viewBox="0 0 38 38" aria-hidden="true">
        <circle cx="19" cy="19" r="18" fill="var(--sky)"/>
        <g fill="none" stroke="var(--navy)" stroke-width="1.6">
          <circle cx="19" cy="19" r="10"/>
          <ellipse cx="19" cy="19" rx="4.5" ry="10"/>
          <line x1="9" y1="19" x2="29" y2="19"/>
          <line x1="11" y1="14" x2="27" y2="14"/>
          <line x1="11" y1="24" x2="27" y2="24"/>
        </g>
      </svg>
      <span>www.<span class="domain">goplainway-example</span>.com</span>
    </div>
  </main>
</body>
</html>
```